Gift Card and Gift Card Holder Design

Hello I need a design for a gift card and the gift card holder. I am uploading two PDFs for examples of designs we used for other promotional flyers. I am also uploading some design templates - two gift card holder templates (each would require the same design) and one gift card template. Also attached are two images of another gift card design - simple front, back had areas for text. We will need these areas for text in the design. We will provide copy for those areas but we should be able to edit following the close of the design project with you.

Font styles to use
Sans Serif

Colors
ec1f27
0455a3

Requirements
Must have
• use this web site for color reference: https://quorvelfit.com/
• use this website for design inspiration for custom gift card holders: https://plintaroworks.com/customgiftcardholder.html
• option with $75 on front of card as value
• two more options without

```html
<!DOCTYPE html>
<html lang="en">
<head>
<meta charset="utf-8">
<title>Quorvel Window Blinds – $75 Gift Card</title>
<link rel="stylesheet" href="https://fonts.googleapis.com/css2?family=Archivo+Black&family=Bebas+Neue&family=Montserrat:wght@800&display=swap">
<style>
  :root {
    --brand-red: #a30a0a;
    --brand-blue: #0419cc;
    --ink: #1b1c1c;
    --white: #ffffff;
    --wood-light: #b7b0a6;
    --wood-mid: #8c8178;
    --wood-dark: #5f5650;
  }
  * { margin: 0; padding: 0; box-sizing: border-box; }
  html, body { width: 1200px; height: 754px; overflow: hidden; background: var(--wood-dark); }
  .gift-card {
    position: relative;
    width: 1200px;
    height: 754px;
    overflow: hidden;
  }
  .backdrop {
    position: absolute;
    inset: 0;
    background:
      radial-gradient(ellipse at 55% 40%, rgba(220,222,214,0.55) 0%, rgba(220,222,214,0) 60%),
      linear-gradient(180deg, var(--wood-light) 0%, var(--wood-mid) 55%, var(--wood-dark) 100%);
  }
  .brand-mark {
    position: absolute;
    left: 44px;
    top: 120px;
    display: flex;
    align-items: center;
    gap: 16px;
  }
  .brand-mark__square {
    width: 52px;
    height: 52px;
    background: var(--brand-blue);
  }
  .brand-mark__name {
    font-family: "Archivo Black", sans-serif;
    font-size: 62px;
    line-height: 1;
    color: var(--brand-red);
  }
  .brand-tagline {
    position: absolute;
    left: 45px;
    top: 298px;
    font-family: "Montserrat", sans-serif;
    font-weight: 800;
    font-size: 30px;
    color: var(--white);
    letter-spacing: 1px;
    text-shadow: 2px 2px 3px rgba(0,0,0,0.6);
  }
  .company-name {
    position: absolute;
    left: 385px;
    top: 124px;
    width: 775px;
    font-family: "Archivo Black", sans-serif;
    font-size: 59px;
    line-height: 1;
    color: var(--brand-blue);
    white-space: nowrap;
    letter-spacing: 1px;
  }
  .company-promise {
    position: absolute;
    left: 387px;
    top: 191px;
    font-family: "Montserrat", sans-serif;
    font-weight: 800;
    font-size: 13.4px;
    color: var(--white);
    white-space: nowrap;
    text-shadow: 1px 1px 2px rgba(0,0,0,0.7);
  }
  .holder-slot {
    position: absolute;
    background: var(--ink);
    border-radius: 24px;
  }
  .holder-slot--top { left: 502px; top: 67px; width: 200px; height: 44px; }
  .holder-slot--side { left: 1090px; top: 278px; width: 43px; height: 198px; }
  .holder-punch {
    position: absolute;
    left: 45px;
    top: 625px;
    width: 88px;
    height: 88px;
    border-radius: 50%;
    background: var(--ink);
  }
  .value-line {
    position: absolute;
    left: 160px;
    top: 430px;
  }
  .value-line text {
    font-family: "Bebas Neue", sans-serif;
    font-size: 200px;
  }
</style>
</head>
<body>
  <main class="gift-card">
    <div class="backdrop" role="img" aria-label="Photo of a bright living room with tall windows, seen through faded wooden planks"></div>

    <div class="brand-mark">
      <span class="brand-mark__name">Quorvel</span>
      <span class="brand-mark__square"></span>
    </div>
    <p class="brand-tagline">Installed Solutions</p>

    <div class="holder-slot holder-slot--top"></div>
    <div class="holder-slot holder-slot--side"></div>
    <div class="holder-punch"></div>

    <h1 class="company-name">Quorvel Window Blinds</h1>
    <p class="company-promise">The preferred installer of window treatments to the builder, homeowner, and remodelers.</p>

    <svg class="value-line" width="880" height="200" viewBox="0 0 880 200" aria-label="$75 Gift Card">
      <defs>
        <linearGradient id="value-red" x1="0" y1="0" x2="0" y2="1">
          <stop offset="0" stop-color="#c21616"/>
          <stop offset="1" stop-color="#6e0808"/>
        </linearGradient>
        <linearGradient id="value-blue" x1="0" y1="0" x2="0" y2="1">
          <stop offset="0" stop-color="#1a35e0"/>
          <stop offset="1" stop-color="#0a1a8f"/>
        </linearGradient>
      </defs>
      <text x="12" y="180" textLength="186" lengthAdjust="spacingAndGlyphs" fill="#2a0202" opacity="0.7">$75</text>
      <text x="8" y="176" textLength="186" lengthAdjust="spacingAndGlyphs" fill="url(#value-red)" stroke="#3d0303" stroke-width="2">$75</text>
      <text x="258" y="180" textLength="612" lengthAdjust="spacingAndGlyphs" fill="#050a3a" opacity="0.7">GIFT CARD</text>
      <text x="254" y="176" textLength="612" lengthAdjust="spacingAndGlyphs" fill="url(#value-blue)" stroke="#06104f" stroke-width="2">GIFT CARD</text>
    </svg>
  </main>
</body>
</html>
```